Start-Up für Training, Coaching & Consulting sucht modernes Webdesign!
Zielgruppe
Wer ist TAVI Training, Coaching & Consulting?
Wir führen Führungskräftetrainings durch, machen Privatkunden für Bewerbungen fit und unterstützen Unternehmen mit Verkaufstrainings. Wir entwickeln Persönlichkeiten im Coaching. Wir beraten Unternehmen und helfen ihnen dabei, ihre Geschäftsabläufe und Prozesse zu optimieren. Dabei steht unsere hohe Qualität im Mittelpunkt - gemeinsam mit unseren kreativen Trainingsmethoden. Unser Background (Diplom-Kaufleute und geprüfte Trainer) bietet dafür die passende Ausgangslage.
Was bedeutet TAVI?
Tavi ist Maori und bdeutet Kreis/Spirale. Er symbolisiert einen wachsenden Silberfarn und steht für persönliche Entwicklung und Entfaltung. Der Tavi ist einerseits unser Namensgeber und unser Logo, andererseits steht der Tavi aber auch für unsere Werte: Denn wir wollen unseren Kunden dabei helfen zu wachsen und sich weiterzuentwickeln - und dies auf eine hochqualitative und seriöse Art und Weise ohne den Eindruck von Esoterik oder Erlebnispädagogik zu vermitteln.
Aufgabenstellung
Modernes Design, das unsere Philosophie widerspiegelt: Wir möchten unseren Kunden auf seriöse und hochqualitative Weise weiterentwickeln. Wir stehen für nachhaltigen Lernerfolg, kreative Trainingsmethoden, Abwechslung, Spaß am Lernen, Qualität, Kompetenz, Fachwissen und Dynamik.
Layout:
1) Header: QMSR geprüfter Trainer, Menüpunkte (siehe Architektur)
2) Banner
3) 3 Teaser (Training, Coaching, Consulting) + Header + 2-3 Zeilen Text (+Icons)
>>> Sichtbarer Bereich auf Homepage: Menü, Banner, Teaser
4) "Warum Sie uns wählen sollten": 5 bullet points ohne weiteren Text
5) "Aus unserem Blog": Frame für 3 Blogartikel + Bild + Datum + Header + 2-3 Zeilen Text
6) Alle drei QMSR Logos
7) Footer: Click Us (quick links), Contact Us (Adresse), Follow Us (Pinnwald, ZOLP, Kontaktor)
8) Copyright + Impressum
>>> Das Design soll klar sein, aber nicht zu kantig. Vielmehr sollen abgerundete Ecken und dynamische Elemente genutzt werden.
Architektur:
3 Ebenen:
1) Homepage
2) TAVI, Training, Coaching, Consulting, für Trainer, Kundenstimmen/Referenzen, Kontakt
3) noch zu bestimmende Produktdetailseiten
Texte werden noch erstellt, Layout kann ggf. mit Platzhaltertext gefüllt werden.
Bildmaterial: Logo und vorhandenes Imagebild werden zur Verfügung gestellt. Bilder können ggf. gekauft werden. Vorschläge erwünscht.
Corporate colors:
grün: #a2c61b + monochromatic colors
http://www.tintoskop.de/a2c61b
grau: #474747 + monochromatic colors
http://www.tintoskop.de/474747

```html
<!DOCTYPE html>
<html lang="de">
<head>
<meta charset="utf-8">
<title>TAVI Training, Coaching &amp; Consulting</title>
<link rel="stylesheet" href="https://fonts.googleapis.com/css2?family=Nunito+Sans:wght@300;400;600;700;800&display=swap">
<style>
:root{
  --green:#a2c61b;
  --green-dark:#7fa014;
  --green-pale:#eef5dc;
  --green-soft:#f4f9e6;
  --grey:#474747;
  --grey-dark:#2b2d31;
  --text:#2f2f2f;
  --white:#ffffff;
  --badge:#1f5fae;
}
*{box-sizing:border-box;margin:0;padding:0}
html,body{width:795px;height:1200px;overflow:hidden;background:var(--white)}
body{position:relative;font-family:"Nunito Sans",sans-serif;color:var(--text)}
.abs{position:absolute}

/* header */
.site-header{position:absolute;left:0;top:0;width:795px;height:53px;background:var(--white);z-index:3}
.brand{left:111px;top:12px;display:flex;align-items:center;gap:4px}
.brand-mark{width:14px;height:14px;border-radius:50%;background:var(--green)}
.brand-name{font-size:22px;font-weight:800;color:var(--grey);letter-spacing:1px;line-height:1}
.brand-tag{left:112px;top:40px;font-size:5px;color:var(--grey)}
.cert-badge{left:201px;top:20px;width:67px;height:17px;background:var(--badge);border-radius:1px}
.main-nav{left:302px;top:0;height:53px;font-size:8.3px;color:var(--text)}
.nav-item{position:absolute;top:0;height:53px;line-height:57px;white-space:nowrap}
.nav-item.active{left:0;width:45px;background:var(--green);color:var(--white);text-align:center}
.nav-sep{position:absolute;top:0;line-height:57px;font-size:8px;color:var(--text)}
.chev{color:var(--green);font-weight:800;font-size:7px}

/* hero */
.hero{left:0;top:53px;width:795px;height:280px}
.hero-photo{position:absolute;inset:0;background:radial-gradient(ellipse at 50% 45%,#5e9a2c 0%,#3f7a1f 45%,#2c5e14 100%)}
.hero-wave{position:absolute;left:0;top:0}
.hero-title{left:0;width:795px;top:118px;text-align:center;color:var(--white);font-weight:300;font-size:31px;line-height:35px;letter-spacing:.3px}
.hero-title strong{font-weight:800}
.hero-sub{left:0;width:795px;top:188px;text-align:center;color:var(--white);font-size:13px;font-weight:300}
.hero-btn{left:347px;top:215px;width:99px;height:33px;border-radius:17px;background:var(--green);color:var(--white);font-size:8px;font-weight:700;text-align:center;line-height:33px}
.hero-arrow{top:148px}

/* teasers */
.teasers{left:100px;top:357px;width:587px;height:183px;border-radius:26px;background:var(--green-pale)}
.teaser-icon{width:42px;height:42px;border-radius:50%;background:var(--green);border:2px solid var(--green-pale)}
.teaser-title{font-size:11.5px;font-weight:600;color:var(--green);letter-spacing:.3px}
.teaser-photo{width:160px;height:105px;border-radius:14px}
.teaser-rule{width:142px;border-top:1px dotted #777}
.teaser-text{width:160px;font-size:7px;line-height:10.5px;text-align:center;color:var(--text)}

/* dividers */
.divider-line{height:1px;background:#d8e4b2}
.divider-dot{width:22px;height:22px;border-radius:50%;background:#d6e89a}

/* why */
.section-title{font-size:17px;font-weight:400;color:var(--grey-dark);letter-spacing:.2px}
.why-list{left:118px;top:665px;list-style:none}
.why-list li{display:flex;align-items:center;height:29.7px;font-size:13px;color:var(--text)}
.tick{width:15px;height:15px;border-radius:50%;background:var(--green);margin-right:7px;display:flex;align-items:center;justify-content:center}

/* blog */
.blog-card{left:451px;width:236px;border-radius:10px;background:var(--green-pale)}
.blog-photo{position:absolute;left:17px;width:59px;height:56px;border-radius:6px}
.blog-body{position:absolute;left:84px;top:9px;width:145px}
.blog-title{font-size:7.5px;font-weight:700;color:var(--text);line-height:10px}
.blog-text{font-size:7px;line-height:10.5px;color:var(--text)}
.more-btn{position:absolute;left:81px;width:38px;height:12px;border-radius:6px;background:var(--green);color:var(--white);font-size:6.5px;text-align:center;line-height:12px}

/* partners */
.partner{background:var(--badge)}

/* footer */
.footer-bg{left:0;top:880px}
.foot-title{top:1034px;font-size:8.5px;font-weight:400;color:#c9c9c9;letter-spacing:.3px}
.foot-links{left:139px;top:1056px;list-style:none;font-size:8px;line-height:10.5px;color:#c9c9c9}
.foot-small{font-size:6px;line-height:8.5px;color:#c9c9c9}
.social{width:22px;height:22px;border-radius:50%;background:var(--green);color:var(--white);font-size:9px;font-weight:700;text-align:center;line-height:22px;top:1053px}
.foot-brand{left:575px;top:1054px;display:flex;align-items:center;gap:4px}
.foot-brand .brand-name{color:var(--white)}
.foot-tag{left:575px;top:1082px;font-size:5px;color:#c9c9c9}
.foot-rule{left:118px;top:1135px;width:559px;border-top:1px dotted var(--green)}
.copyright{left:0;width:795px;top:1140px;text-align:center;font-size:8px;line-height:12.5px;font-weight:300;color:#a9a9a9}
.copyright .imprint{color:var(--green)}
</style>
</head>
<body>

<header class="site-header">
  <div class="abs brand"><span class="brand-name">TAVI</span><span class="brand-mark"></span></div>
  <div class="abs brand-tag">Training • Coaching • Consulting</div>
  <div class="abs cert-badge" role="img" aria-label="Partnerzeichen"></div>
  <nav class="abs main-nav" style="width:400px">
    <span class="nav-item active">HOME</span>
    <span class="nav-sep" style="left:51px">I</span>
    <span class="nav-item" style="left:72px">ÜBER UNS <span class="chev">&#8964;</span></span>
    <span class="nav-sep" style="left:130px">I</span>
    <span class="nav-item" style="left:151px">FÜR TRAINERS <span class="chev">&#8964;</span></span>
    <span class="nav-sep" style="left:226px">I</span>
    <span class="nav-item" style="left:247px">REFERENZEN</span>
    <span class="nav-sep" style="left:320px">I</span>
    <span class="nav-item" style="left:341px">KONTAKT</span>
  </nav>
</header>

<section class="abs hero">
  <div class="hero-photo" role="img" aria-label="Bild: sich entrollende grüne Farnwedel"></div>
  <svg class="hero-wave" width="795" height="280" viewBox="0 0 795 280">
    <path d="M0 214 C120 200 260 225 420 258 C560 285 700 240 795 156 L795 280 L0 280 Z" fill="var(--green)"/>
    <path d="M0 236 C130 220 280 240 430 268 C580 292 710 250 795 188 L795 280 L0 280 Z" fill="var(--white)"/>
  </svg>
  <svg class="abs hero-arrow" style="left:48px" width="26" height="44" viewBox="0 0 26 44"><path d="M22 4 L5 22 L22 40" fill="none" stroke="rgba(255,255,255,.55)" stroke-width="6" stroke-linecap="round" stroke-linejoin="round"/></svg>
  <svg class="abs hero-arrow" style="left:721px" width="26" height="44" viewBox="0 0 26 44"><path d="M4 4 L21 22 L4 40" fill="none" stroke="rgba(255,255,255,.55)" stroke-width="6" stroke-linecap="round" stroke-linejoin="round"/></svg>
</section>
<h1 class="abs hero-title">TRAINING, COACHING<br>CONSULTING <strong>FÜR TRAINER</strong></h1>
<p class="abs hero-sub">Lorem ipsum dolor sit amet consectetur adipiscing elit.</p>
<a class="abs hero-btn">MEHR ERFAHREN</a>

<section class="abs teasers"></section>
<div class="abs teaser-photo" style="left:130px;top:390px;background:linear-gradient(160deg,#8fb0d8,#d7dfe8 60%,#6f86a6)" role="img" aria-label="Foto: gefaltete Hände auf einem Notizbuch"></div>
<div class="abs teaser-photo" style="left:316px;top:390px;background:linear-gradient(160deg,#e9ecef,#c9ced4 55%,#3a3f48)" role="img" aria-label="Foto: Beratungsgespräch am Tablet"></div>
<div class="abs teaser-photo" style="left:501px;top:390px;background:linear-gradient(160deg,#cfd9e4,#eef1f4 50%,#a89a8e)" role="img" aria-label="Foto: Besprechung am Konferenztisch"></div>
<div class="abs teaser-icon" style="left:109px;top:368px" role="img" aria-label="Symbol Coaching"></div>
<div class="abs teaser-icon" style="left:294px;top:368px" role="img" aria-label="Symbol Consulting"></div>
<div class="abs teaser-icon" style="left:480px;top:368px" role="img" aria-label="Symbol Training"></div>
<h2 class="abs teaser-title" style="left:177px;top:371px">COACHING</h2>
<h2 class="abs teaser-title" style="left:359px;top:371px">CONSULTING</h2>
<h2 class="abs teaser-title" style="left:553px;top:371px">TRAINING</h2>
<div class="abs teaser-rule" style="left:139px;top:501px"></div>
<div class="abs teaser-rule" style="left:326px;top:501px"></div>
<div class="abs teaser-rule" style="left:511px;top:501px"></div>
<p class="abs teaser-text" style="left:130px;top:505px">Lorem ipsum dolor sit amet, consectetur adipiscing elit. In dapibus accumsan luctus.</p>
<p class="abs teaser-text" style="left:316px;top:505px">Dolor sit amet, consectetur adipiscing elit. In dapibus accumsan luctus.</p>
<p class="abs teaser-text" style="left:501px;top:505px">Sit amet, consectetur adipiscing elit. In dapibus accumsan luctus.</p>

<div class="abs divider-line" style="left:80px;top:583px;width:291px"></div>
<div class="abs divider-line" style="left:424px;top:583px;width:291px"></div>
<div class="abs divider-dot" style="left:386px;top:569px"></div>

<svg class="abs" style="left:0;top:770px" width="400" height="90" viewBox="0 0 400 90">
  <path d="M0 56 C120 78 300 90 397 5 L397 40 C300 92 120 85 0 62 Z" fill="var(--green-soft)"/>
</svg>
<h2 class="abs section-title" style="left:139px;top:621px">WHY CHOOSE US</h2>
<ul class="abs why-list">
  <li><span class="tick"><svg width="6" height="7" viewBox="0 0 6 7"><path d="M1.5 1 L4.5 3.5 L1.5 6" fill="none" stroke="#fff" stroke-width="1.4"/></svg></span>Vestibulum nec mauris facilisis</li>
  <li><span class="tick"><svg width="6" height="7" viewBox="0 0 6 7"><path d="M1.5 1 L4.5 3.5 L1.5 6" fill="none" stroke="#fff" stroke-width="1.4"/></svg></span>Curabitur et tristique diam, nec sagittis nibh</li>
  <li><span class="tick"><svg width="6" height="7" viewBox="0 0 6 7"><path d="M1.5 1 L4.5 3.5 L1.5 6" fill="none" stroke="#fff" stroke-width="1.4"/></svg></span>Denim nec sagittis nibh</li>
  <li><span class="tick"><svg width="6" height="7" viewBox="0 0 6 7"><path d="M1.5 1 L4.5 3.5 L1.5 6" fill="none" stroke="#fff" stroke-width="1.4"/></svg></span>Vestibulum nec mauris facilisis</li>
  <li><span class="tick"><svg width="6" height="7" viewBox="0 0 6 7"><path d="M1.5 1 L4.5 3.5 L1.5 6" fill="none" stroke="#fff" stroke-width="1.4"/></svg></span>Tristique diam nec lorem</li>
</ul>

<h2 class="abs section-title" style="left:469px;top:621px">BLOG</h2>
<article class="abs blog-card" style="top:653px;height:71px">
  <div class="blog-photo" style="top:9px;background:linear-gradient(160deg,#e6e9ec,#3a3f48)" role="img" aria-label="Foto: Beratungsgespräch"></div>
  <div class="blog-body"><h3 class="blog-title">08.12.2015 Sit Amet Adipiscing</h3><p class="blog-text">Lorem ipsum dolor sit amet, consectetur adipiscing elit. In dapibus accumsan luctus. Aliquam posuere eros sed nibh sagittis,</p></div>
  <span class="more-btn" style="top:53px">more</span>
</article>
<article class="abs blog-card" style="top:730px;height:70px">
  <div class="blog-photo" style="top:9px;background:linear-gradient(160deg,#cfd9e4,#eef1f4 50%,#a89a8e)" role="img" aria-label="Foto: Besprechung"></div>
  <div class="blog-body"><h3 class="blog-title">08.12.2015 Lorem Ipsum Dolor</h3><p class="blog-text">Pellentesque habitant morbi tristique senectus et netus et malesuada fames ac turpis egestas.</p></div>
  <span class="more-btn" style="top:53px">more</span>
</article>
<article class="abs blog-card" style="top:805px;height:72px">
  <div class="blog-photo" style="top:9px;background:linear-gradient(160deg,#8fb0d8,#d7dfe8 60%,#6f86a6)" role="img" aria-label="Foto: gefaltete Hände"></div>
  <div class="blog-body"><h3 class="blog-title">08.12.2015 Adipiscing Vehicula</h3><p class="blog-text">Mauris sollicitudin felis aliquam ipsum dictum vehicula. Donec feugiat sapien nunc, quis auctor libero finibus in.</p></div>
  <span class="more-btn" style="top:56px">more</span>
</article>

<div class="abs divider-line" style="left:80px;top:885px;width:291px"></div>
<div class="abs divider-line" style="left:424px;top:885px;width:291px"></div>
<div class="abs divider-dot" style="left:386px;top:871px"></div>

<svg class="abs footer-bg" width="795" height="320" viewBox="0 0 795 320">
  <path d="M0 72 C150 86 300 120 460 126 C620 130 720 70 795 13 L795 320 L0 320 Z" fill="var(--green)"/>
  <path d="M0 92 C160 100 300 132 470 133 C630 134 730 80 795 30 L795 320 L0 320 Z" fill="var(--grey-dark)"/>
</svg>
<div class="abs partner" style="left:273px;top:937px;width:66px;height:18px" role="img" aria-label="Partnerzeichen"></div>
<div class="abs partner" style="left:368px;top:930px;width:24px;height:30px" role="img" aria-label="Partnerzeichen"></div>
<div class="abs partner" style="left:448px;top:930px;width:24px;height:30px" role="img" aria-label="Partnerzeichen"></div>

<h3 class="abs foot-title" style="left:139px">CLICK US</h3>
<h3 class="abs foot-title" style="left:249px">CONTACT US</h3>
<h3 class="abs foot-title" style="left:476px">FOLLOW US</h3>
<ul class="abs foot-links"><li>Home</li><li>Über uns</li><li>Für trainers</li><li>Referenzen</li><li>Kontakt</li></ul>
<svg class="abs" style="left:230px;top:1056px" width="14" height="12" viewBox="0 0 14 12"><path d="M7 0 L14 6 L12 6 L12 12 L8.5 12 L8.5 8 L5.5 8 L5.5 12 L2 12 L2 6 L0 6 Z" fill="var(--green)"/></svg>
<p class="abs foot-small" style="left:250px;top:1057px">Vestibulum nec mauris 62<br>Suscipit est et<br>62134 Townname</p>
<svg class="abs" style="left:340px;top:1057px" width="12" height="12" viewBox="0 0 12 12"><rect width="12" height="12" rx="2" fill="var(--green)"/><path d="M3.5 2.5 L5 4.5 L4.2 5.5 C4.8 6.6 5.5 7.3 6.5 7.8 L7.5 7 L9.5 8.5 L8.6 9.7 C6 9.5 2.7 6.3 2.4 3.4 Z" fill="var(--grey-dark)"/></svg>
<p class="abs foot-small" style="left:357px;top:1057px">000 123 7658 903<br>(000 123 7658 903</p>
<svg class="abs" style="left:339px;top:1081px" width="13" height="9" viewBox="0 0 13 9"><rect width="13" height="9" rx="1" fill="var(--green)"/><path d="M0.5 0.8 L6.5 5 L12.5 0.8" fill="none" stroke="var(--grey-dark)" stroke-width="1"/></svg>
<p class="abs foot-small" style="left:357px;top:1083px">info@tavi.com</p>
<span class="abs social" style="left:462px" role="img" aria-label="Pinnwald">P</span>
<span class="abs social" style="left:491px" role="img" aria-label="Piepser">P</span>
<span class="abs social" style="left:521px" role="img" aria-label="Kontaktor">K</span>
<div class="abs foot-brand"><span class="brand-name">TAVI</span><span class="brand-mark"></span></div>
<div class="abs foot-tag">Training • Coaching • Consulting</div>

<div class="abs foot-rule"></div>
<p class="abs copyright"><span class="imprint">Copyright + Impressum</span><br>Aliquam at pulvinar mi. Nulla eget bibendum nisl. Integer consectetur quam ac purus pharetra pulvinar.<br>Aenean faucibus tortor ac tortor aliquet tincidunt. Mauris eget maximus urna.</p>

</body>
</html>
```